Company or website name
- Velmira, LLC
- Velmira, LLC
- Describe your company and organization and target audience
- Velmira, LLC is a research, science and technology based manufacturing company that formulates, develops, manufactures and packages a full complement of personal care products for domestic and international concerns. We private label and contract package personal care products, cosmetics, bath salts and powders and home fragrance products. Velmira is conveniently located in Southern California adjacent to major transportation hubs and international airports. We utilize earth friendly, green manufacturing processes, maximize the use of renewable resource raw materials and minimize the use of non-renewable and petrochemical based raw materials. We provide formulation and product development services with low minimum order quantities and short lead times. Velmira is the intersection between nature, science, beauty and innovation. We are a B-2-B company.
- The design should have the following
- We're looking for an ad design that can be used for both banner and column use online and in print. We manufacture bath and body products such as bath salts, body washes, body powders, bath oils and bubble baths, hair care products such as shampoos, conditioners and styling aids, skin care products such as anti-aging creams, cleansers, masks, toners and serums, color cosmetics such as eyeliners, mascaras, foundations and mineral make-up powders, manicure/pedicure products such as cuticle oils, sugar and salt scrubs and foot soaks/softeners and spa products such as seaweed wraps, cellulite creams, body masks, massage oils and candles. Our strengths are natural and organic product formulation, low minimums, competitive prices, complete research &development services new and innovative ingredients and fast turnaround times. Examples can be found at the following sites: http://www.glintor.com/ http://www.grovewellboard.org/ http://www.tessaloomjournal.com/ http://nerwast.org/images/downloads/bulletins/2009-10-bulletin.pdf http://www.pantrykestrelworks.com/

```html
<!DOCTYPE html>
<html lang="en">
<head>
<meta charset="utf-8">
<title>Velmira, LLC — Natural Organic Product</title>
<link rel="stylesheet" href="https://fonts.googleapis.com/css2?family=Titillium+Web:wght@600;700&display=swap">
<style>
  :root {
    --lime: #b3d800;
    --lime-light: #c2e000;
    --green-deep: #3d9a06;
    --ink: #111a05;
    --white: #ffffff;
    --rule: rgba(40, 90, 0, 0.55);
    --photo-light: #d9ddd6;
    --photo-leaf: #5f9a2c;
    --photo-wood: #8a8c86;
  }
  * { margin: 0; padding: 0; box-sizing: border-box; }
  html, body { width: 1200px; height: 529px; overflow: hidden; background: var(--white); }
  .banner {
    position: relative;
    width: 1200px;
    height: 529px;
    font-family: "Titillium Web", sans-serif;
    overflow: hidden;
  }
  .banner__photo {
    position: absolute;
    left: 0; top: 0;
    width: 794px; height: 529px;
    background:
      radial-gradient(ellipse at 22% 45%, var(--photo-leaf) 0%, rgba(95,154,44,0.6) 30%, rgba(95,154,44,0) 60%),
      radial-gradient(ellipse at 65% 60%, rgba(196,130,30,0.65) 0%, rgba(196,130,30,0) 35%),
      linear-gradient(180deg, var(--photo-light) 0%, #c9cec4 55%, var(--photo-wood) 100%);
  }
  .banner__panel {
    position: absolute;
    left: 794px; top: 0;
    width: 406px; height: 529px;
    background: linear-gradient(180deg, var(--lime-light) 0%, #9ccd00 45%, var(--green-deep) 100%);
  }
  .tag {
    position: absolute;
    background: var(--lime);
    border: 4px solid var(--white);
    color: var(--ink);
    font-weight: 700;
    text-transform: uppercase;
    display: flex;
    align-items: center;
    justify-content: center;
    white-space: nowrap;
    box-shadow: 0 2px 6px rgba(0,0,0,0.25);
  }
  .tag--headline {
    left: 639px; top: 33px;
    width: 528px; height: 70px;
    font-size: 36px;
    letter-spacing: 0.5px;
  }
  .tag--footer {
    left: 11px; top: 441px;
    width: 1156px; height: 70px;
    font-size: 37px;
    letter-spacing: 0.3px;
  }
  .strengths {
    position: absolute;
    left: 828px; top: 120px;
    width: 324px;
    list-style: none;
  }
  .strengths__item {
    height: 77px;
    display: flex;
    align-items: center;
    justify-content: center;
    color: var(--white);
    font-weight: 700;
    font-size: 27px;
    letter-spacing: 0.5px;
    text-transform: uppercase;
    text-shadow: 1px 2px 3px rgba(0,0,0,0.45);
    white-space: nowrap;
    border-bottom: 2px solid var(--rule);
  }
  .strengths__item:last-child { border-bottom: none; }
</style>
</head>
<body>
  <main class="banner">
    <div class="banner__photo" role="img" aria-label="Fresh mint leaves in a wicker basket beside amber and clear essential oil bottles on a wooden table"></div>
    <div class="banner__panel"></div>

    <h1 class="tag tag--headline">Natural Organic Product</h1>

    <ul class="strengths">
      <li class="strengths__item">Low Minimums</li>
      <li class="strengths__item">Competitive Prices</li>
      <li class="strengths__item">Complete Research</li>
      <li class="strengths__item">Development Services</li>
    </ul>

    <p class="tag tag--footer">New and Innovative Ingredients and Fast Turnaround Times</p>
  </main>
</body>
</html>
```